Public Relations Agency Seeks Wordpress Design and Coding

TRELVOX Studio is a public relations agency specializing in media relations, public affairs and marketing communication.

The site should display the following visual characteristics: professionalism, trustworthiness, high-tech focus, clear and concise design.

The desired colors are royal blue, gray and hints of red.

Design look/feel inspired by this site: http://brightpathgatherings.example/

Specifications:

1. Navigation/Pages/Index:

HOME

ABOUT US

SERVICES

NEWS

CONTACT

---

2. Functionality of/content for each page:

- Home
o Dominant photo (professional, edgy, innovative)
o Simple, straightforward access to/from “Home” from other pages
o Includes logo (attached) and tagline "Unleash the power of communication"
o Direct link to “CONTACT”
o Links to social media accounts: Facebook, Twitter, LinkedIn

- About Us

o Company profile blurb
o President’s photo with short bio

- Services
o Public Relations
 Strategic communication
 Brand and reputation management
 Community relations
o Media Relations
 News coverage and contacts
 Media training and interview skills
 Crisis communications
o Congressional Affairs
 Public affairs
 Public policy
 Legislative strategy
o Mass Communication
 Speechwriting
 Presentation creation
 Social media
o Marketing Communications
 Business collateral material
 Promotional campaigns
 Special events and tradeshows

- News
o Blog-like page to post information and/or share news from other sites

- Contact
o Standard “Contact Us” form (Name, Email, Phone, Message)
o Direct Contact
 (407) 555-0164
 info@TRELVOXstudio.example

Target Market(s)

Small to large businesses specializing in high technology, defense/military, medicine/healthcare, and wide array of professional services.

Industry/Entity Type

Marketing

Font styles to use
Serif
Sans Serif

Colors
0555a3
ec2027
edf3f7

Requirements
Must have
• -- Project reqires DESIGN - and - fully CODED.

-- Strong SEO

-- Optimized for mobile viewing

Thank you!

```html
<!DOCTYPE html>
<html lang="en">
<head>
<meta charset="utf-8">
<title>TRELVOX Studio — Public Relations</title>
<link rel="stylesheet" href="https://fonts.googleapis.com/css2?family=Raleway:wght@300;400;600;700&family=Open+Sans:wght@400;600;700&display=swap">
<style>
:root{
  --blue:#0555a3;
  --red:#ec2027;
  --mist:#edf3f7;
  --sky:#dcecf5;
  --ink:#2e3338;
  --muted:#8a949c;
  --line:#e2e7eb;
  --slate:#5b6b79;
  --slate-dark:#4c5a67;
  --white:#ffffff;
}
*{box-sizing:border-box;margin:0;padding:0}
html,body{width:1200px;height:4528px;overflow:hidden}
body{font-family:"Open Sans",Arial,sans-serif;color:var(--ink);background:var(--white);font-size:13px;line-height:1.6}
h1,h2,h3,h4{font-family:"Raleway",Helvetica,sans-serif;font-weight:400}
.wrap{width:880px;margin:0 auto;position:relative}
.section-title{text-align:center;font-size:30px;color:var(--ink)}
.section-sub{text-align:center;font-size:11px;color:var(--muted);margin-top:6px}
.btn{display:inline-block;font-size:11px;font-weight:600;padding:8px 18px;border-radius:2px;text-decoration:none;white-space:nowrap}
.btn-blue{background:var(--blue);color:var(--white)}
.btn-red{background:var(--red);color:var(--white)}
.btn-ghost{background:var(--white);color:var(--blue);border:1px solid var(--line)}
.eyebrow{font-size:12px;color:var(--blue);font-weight:600}

/* hero */
.hero{position:relative;height:600px;background:linear-gradient(160deg,#3c3a37 0%,#5d5a55 35%,#8a8780 55%,#3a3835 100%)}
.site-header{position:absolute;top:0;left:0;right:0;height:70px;display:flex;align-items:center;justify-content:space-between;padding:0 90px;z-index:2}
.brand{display:flex;align-items:center;gap:10px;color:var(--white);font-family:"Raleway",sans-serif;font-weight:700;font-size:22px;letter-spacing:1px}
.brand-mark{width:20px;height:20px;background:var(--blue)}
.main-nav{display:flex;gap:36px}
.main-nav a{color:var(--white);text-decoration:none;font-size:14px}
.hero-photo{position:absolute;inset:0}
.hero-tagline{position:absolute;left:160px;top:300px;color:var(--white);font-family:"Raleway",sans-serif;font-size:34px;line-height:1.3;font-weight:600}
.hero-tagline strong{font-weight:700;display:block}
.slider-arrow{position:absolute;top:320px;width:20px;height:30px}
.slider-arrow.left{left:90px}
.slider-arrow.right{right:90px}

/* promo */
.promo{height:140px;display:flex;align-items:center;border-bottom:1px solid var(--line)}
.promo .wrap{display:flex;justify-content:space-between;align-items:center}
.promo h2{font-size:24px}
.promo h2 span{color:var(--blue)}
.promo p{font-size:11px;color:var(--muted);margin-top:4px}
.promo .btn{min-width:90px;text-align:center}

/* features */
.features{height:460px;padding-top:50px}
.feature-grid{display:flex;gap:20px}
.feature-card{flex:1;background:var(--mist);border:1px solid var(--line);height:350px;text-align:center;padding:30px}
.feature-card h3{font-size:15px;font-weight:600;margin-bottom:22px}
.feature-icon{width:60px;height:60px;margin:0 auto 20px;display:block}
.feature-card p{font-size:11px;color:var(--muted);margin-bottom:28px}

/* about */
.about{height:510px;background:var(--mist);padding-top:55px}
.about .wrap{display:flex;gap:50px}
.portrait{width:300px;height:380px;background:linear-gradient(180deg,#3a5c8c 0%,#c8b7a8 45%,#b3262c 100%)}
.about-body{flex:1;padding-top:20px}
.about-body h2{font-size:28px;line-height:1.25;margin:10px 0 26px;width:380px}
.point{display:flex;gap:22px;margin-bottom:26px;align-items:flex-start}
.point svg{flex:none}
.point p{font-size:11px;color:var(--muted);width:340px}

/* news */
.news{height:450px;padding-top:45px}
.news-grid{display:flex;gap:20px;margin-top:40px}
.news-item{flex:1}
.news-thumb{height:215px}
.news-item h4{font-family:"Open Sans",sans-serif;font-size:11px;font-weight:600;margin-top:12px}
.news-item time{font-size:10px;color:var(--blue)}

/* product */
.product{height:580px;background:var(--sky);padding-top:60px}
.product .wrap{display:flex;justify-content:space-between}
.product-copy{width:430px}
.product-copy h2{font-size:30px;line-height:1.25;margin:12px 0 26px}
.product-copy p{font-size:11px;color:var(--muted)}
.tick-list{list-style:none;margin:24px 0}
.tick-list li{display:flex;gap:14px;font-size:11px;color:var(--muted);margin-bottom:14px;align-items:flex-start}
.tick-list svg{flex:none}
.product-actions{display:flex;gap:10px}
.device-shot{width:380px;height:440px;border-radius:24px;background:linear-gradient(150deg,#1d2125 0%,#3a434c 50%,#15181b 100%)}

/* cases */
.cases{height:420px;padding-top:48px}
.case-mosaic{margin-top:40px;height:260px;display:grid;grid-template-columns:repeat(10,1fr);grid-template-rows:1fr 1fr;overflow:hidden}
.case-mosaic div:nth-child(1){grid-row:span 2;grid-column:span 2}
.case-mosaic div:nth-child(6){grid-row:span 2;grid-column:span 2}

/* testimonials */
.testimonials{height:460px;padding-top:50px}
.quote-band{margin-top:40px;height:300px;background:var(--mist);padding-top:60px;text-align:center}
.quote-band blockquote{width:700px;margin:0 auto;font-size:12px;color:var(--muted);font-style:italic}
.quote-band cite{display:block;margin-top:22px;font-style:normal;font-size:11px;font-weight:600;color:var(--ink)}
.avatars{display:flex;justify-content:center;gap:12px;margin-top:14px}
.avatar{width:44px;height:44px;border-radius:50%;background:#c6ccd2}
.avatar.active{background:#9aa6b1}

/* work */
.work{height:470px;padding-top:55px}
.client-grid{display:grid;grid-template-columns:repeat(5,1fr);row-gap:50px;margin-top:55px}
.client{display:flex;align-items:center;justify-content:center;gap:8px;font-family:"Raleway",sans-serif;font-weight:700;font-size:15px;color:#6b7680;letter-spacing:1px}
.client i{width:12px;height:12px;background:var(--red);border-radius:50%}

/* footer */
.site-footer{height:380px;background:var(--slate);color:#dce3e9;padding-top:40px}
.contact-strip{display:flex;gap:60px;align-items:center;padding-bottom:30px;border-bottom:1px solid rgba(255,255,255,.15)}
.contact-item{display:flex;gap:12px;align-items:center;font-size:11px;white-space:nowrap}
.contact-item b{display:block;color:var(--white);font-size:12px}
.socials{margin-left:auto;display:flex;gap:6px}
.socials span{width:24px;height:24px;border:1px solid rgba(255,255,255,.4)}
.footer-cols{display:flex;gap:60px;margin-top:30px}
.footer-cols section{flex:1}
.footer-cols h4{font-size:13px;color:#7fb7ea;font-weight:600;margin-bottom:12px}
.footer-cols p,.footer-cols li{font-size:11px;list-style:none;margin-bottom:8px}
.footer-cols time{display:block;font-size:10px;color:#aebcc8}
.bottom-bar{height:58px;background:var(--slate-dark);color:#c3cdd6;font-size:11px}
.bottom-bar .wrap{display:flex;justify-content:space-between;align-items:center;height:58px}
.bottom-bar nav{display:flex;gap:20px}
</style>
</head>
<body>

<header class="hero">
  <div class="hero-photo" role="img" aria-label="Photo of an open hand reaching into falling water"></div>
  <div class="site-header">
    <div class="brand"><span class="brand-mark"></span>TRELVOX Studio</div>
    <nav class="main-nav"><a href="#">Home</a><a href="#">About Us</a><a href="#">Services</a><a href="#">News</a><a href="#">Contact</a></nav>
  </div>
  <h1 class="hero-tagline">Unleash the power <strong>of communication</strong></h1>
  <svg class="slider-arrow left" viewBox="0 0 20 30"><path d="M14 5 L5 15 L14 25" fill="none" stroke="#fff" stroke-width="3"/></svg>
  <svg class="slider-arrow right" viewBox="0 0 20 30"><path d="M6 5 L15 15 L6 25" fill="none" stroke="#fff" stroke-width="3"/></svg>
</header>

<section class="promo">
  <div class="wrap">
    <div>
      <h2>Hear more about our <span>new promotion</span></h2>
      <p>We offer tailored media plans that help your brand reach the right people at the right time.</p>
    </div>
    <a class="btn btn-red" href="#">Get Started</a>
  </div>
</section>

<section class="features">
  <div class="wrap feature-grid">
    <article class="feature-card">
      <h3>Responsive Ready</h3>
      <svg class="feature-icon" viewBox="0 0 60 60"><rect x="10" y="14" width="40" height="26" rx="2" fill="none" stroke="#0555a3" stroke-width="2.5"/><path d="M24 46 H36 M30 40 V46" stroke="#0555a3" stroke-width="2.5"/></svg>
      <p>Layouts that adapt smoothly to every screen, from wide desktops down to compact phones.</p>
      <a class="btn btn-blue" href="#">Get More</a>
    </article>
    <article class="feature-card">
      <h3>Powerful Admin</h3>
      <svg class="feature-icon" viewBox="0 0 60 60"><path d="M12 14 H48 V38 H26 L16 46 V38 H12 Z" fill="none" stroke="#0555a3" stroke-width="2.5" stroke-linejoin="round"/></svg>
      <p>Manage pages, posts and media from one clean dashboard built for busy teams.</p>
      <a class="btn btn-blue" href="#">Get More</a>
    </article>
    <article class="feature-card">
      <h3>Deeply Customizable</h3>
      <svg class="feature-icon" viewBox="0 0 60 60"><path d="M44 10 L26 32 M22 34 C16 36 16 44 12 48 C20 48 28 46 30 40 Z" fill="none" stroke="#0555a3" stroke-width="2.5" stroke-linejoin="round"/></svg>
      <p>Adjust colours, fonts and sections to shape a site that fits your voice.</p>
      <a class="btn btn-blue" href="#">Get More</a>
    </article>
  </div>
</section>

<section class="about">
  <div class="wrap">
    <div class="portrait" role="img" aria-label="Portrait of the agency president in a red jacket beside a flag"></div>
    <div class="about-body">
      <span class="eyebrow">Our continued innovation</span>
      <h2>The product launch area and other awesome cotent</h2>
      <div class="point">
        <svg width="30" height="30" viewBox="0 0 30 30"><path d="M22 4 L12 16 M10 18 C6 19 6 24 4 26 C9 26 13 25 14 21 Z" fill="none" stroke="#0555a3" stroke-width="2"/></svg>
        <p>Our team builds clear messages that carry your story to reporters, partners and the wider public.</p>
      </div>
      <div class="point">
        <svg width="30" height="30" viewBox="0 0 30 30"><circle cx="15" cy="15" r="6" fill="none" stroke="#0555a3" stroke-width="2"/><path d="M15 3 V7 M15 23 V27 M3 15 H7 M23 15 H27 M6.5 6.5 L9.5 9.5 M20.5 20.5 L23.5 23.5 M6.5 23.5 L9.5 20.5 M20.5 9.5 L23.5 6.5" stroke="#0555a3" stroke-width="2"/></svg>
        <p>We plan each campaign around measurable goals, tracking reach and response at every step.</p>
      </div>
      <div class="point">
        <svg width="30" height="30" viewBox="0 0 30 30"><rect x="5" y="8" width="20" height="14" rx="1" fill="none" stroke="#0555a3" stroke-width="2"/><path d="M5 8 L15 16 L25 8" fill="none" stroke="#0555a3" stroke-width="2"/></svg>
        <p>From briefings to crisis response, we stand beside your leaders when the spotlight turns on.</p>
      </div>
    </div>
  </div>
</section>

<section class="news">
  <h2 class="section-title">Meet the press news area</h2>
  <p class="section-sub">Recent coverage, announcements and stories from the people and projects we support.</p>
  <div class="wrap news-grid">
    <article class="news-item">
      <div class="news-thumb" role="img" aria-label="Misty landscape photo" style="background:linear-gradient(160deg,#d9d3c4,#8c8673)"></div>
      <h4>Regional forum draws record attendance this spring</h4><time>March 12, 2015</time>
    </article>
    <article class="news-item">
      <div class="news-thumb" role="img" aria-label="Sunlit forest photo" style="background:linear-gradient(160deg,#f0d9a8,#6e5232)"></div>
      <h4>Health partners launch new outreach program</h4><time>March 09, 2015</time>
    </article>
    <article class="news-item">
      <div class="news-thumb" role="img" aria-label="Warm sunset field photo" style="background:linear-gradient(160deg,#c98c5b,#3e2a25)"></div>
      <h4>Defense tech summit opens to press</h4><time>March 05, 2015</time>
    </article>
    <article class="news-item">
      <div class="news-thumb" role="img" aria-label="Night street lights photo" style="background:linear-gradient(160deg,#2b3036,#7c6a3e)"></div>
      <h4>Evening gala raises funds for local schools</h4><time>March 02, 2015</time>
    </article>
  </div>
</section>

<section class="product">
  <div class="wrap">
    <div class="product-copy">
      <span class="eyebrow">Our continued innovation</span>
      <h2>The product launch area and other awesome cotent</h2>
      <p>Every launch deserves a clear plan. We shape the message, prepare the spokespeople and line up the coverage so your new product arrives with the attention it has earned. Our team handles timing, outreach and follow up from the first draft to the final report.</p>
      <ul class="tick-list">
        <li><svg width="18" height="18" viewBox="0 0 18 18"><path d="M3 9 L7 13 L15 4" fill="none" stroke="#0555a3" stroke-width="2"/></svg>Launch timelines mapped to press cycles and industry events.</li>
        <li><svg width="18" height="18" viewBox="0 0 18 18"><path d="M3 9 L7 13 L15 4" fill="none" stroke="#0555a3" stroke-width="2"/></svg>Media kits, briefings and interview prep for every spokesperson.</li>
      </ul>
      <div class="product-actions"><a class="btn btn-ghost" href="#">Purchase</a><a class="btn btn-blue" href="#">Get More Info</a></div>
    </div>
    <div class="device-shot" role="img" aria-label="Two smartphones showing an analytics dashboard"></div>
  </div>
</section>

<section class="cases">
  <h2 class="section-title">Client case study examples</h2>
  <p class="section-sub">A look at selected campaigns and the results we delivered for our clients.</p>
  <div class="case-mosaic" role="img" aria-label="Mosaic of client campaign photos">
    <div style="background:#4a5560"></div><div style="background:#8c7a66"></div><div style="background:#2f3a44"></div><div style="background:#b49b7e"></div><div style="background:#5d6e5a"></div>
    <div style="background:#7fc0c6"></div><div style="background:#3d3630"></div><div style="background:#a6a39a"></div><div style="background:#58483c"></div><div style="background:#2b2e33"></div>
    <div style="background:#9b6b4c"></div><div style="background:#6f7b86"></div><div style="background:#c9b79b"></div><div style="background:#46423c"></div>
  </div>
</section>

<section class="testimonials">
  <h2 class="section-title">What our client are saying</h2>
  <p class="section-sub">Kind words from partners who trusted us with their voice and their reputation.</p>
  <div class="quote-band">
    <blockquote>Working with this team changed the way we talk to the press. They listened first, then gave us a plan that was simple to follow and easy to measure. Our coverage doubled within a season, and our staff now feel ready for every interview that comes their way.</blockquote>
    <cite>Odile Marchetti</cite>
    <div class="avatars">
      <span class="avatar" role="img" aria-label="Client portrait"></span>
      <span class="avatar active" role="img" aria-label="Client portrait"></span>
      <span class="avatar" role="img" aria-label="Client portrait"></span>
    </div>
  </div>
</section>

<section class="work">
  <h2 class="section-title">What we have done</h2>
  <p class="section-sub">Brands and organisations we have partnered with across technology, health and public service.</p>
  <div class="wrap client-grid">
    <div class="client"><i></i>NORVALE</div>
    <div class="client"><i></i>CASTREL</div>
    <div class="client"><i></i>PINEWICK</div>
    <div class="client"><i></i>VELTRANE</div>
    <div class="client"><i></i>OSTRELO</div>
    <div class="client"><i></i>ORAMAY</div>
    <div class="client"><i></i>QUILLON</div>
    <div class="client"><i></i>SABLERUN</div>
    <div class="client"><i></i>HARROWIN</div>
    <div class="client"><i></i>BRINDLE</div>
  </div>
</section>

<footer class="site-footer">
  <div class="wrap">
    <div class="contact-strip">
      <div class="contact-item">
        <svg width="26" height="26" viewBox="0 0 26 26"><path d="M7 4 L11 4 L12 9 L9.5 10.5 C11 13.5 12.5 15 15.5 16.5 L17 14 L22 15 L22 19 C22 20.5 21 21.5 19.5 21.5 C11 21 5 15 4.5 6.5 C4.5 5 5.5 4 7 4 Z" fill="none" stroke="#fff" stroke-width="1.6"/></svg>
        <div><b>(407) 555-0164</b>Phone number</div>
      </div>
      <div class="contact-item">
        <svg width="26" height="26" viewBox="0 0 26 26"><rect x="3" y="6" width="20" height="14" fill="none" stroke="#fff" stroke-width="1.6"/><path d="M3 6 L13 14 L23 6" fill="none" stroke="#fff" stroke-width="1.6"/></svg>
        <div><b>info@TRELVOXstudio.example</b>Email address</div>
      </div>
      <div class="contact-item">
        <svg width="26" height="26" viewBox="0 0 26 26"><circle cx="13" cy="13" r="9" fill="none" stroke="#fff" stroke-width="1.6"/><path d="M13 8 V13 L17 15" fill="none" stroke="#fff" stroke-width="1.6"/></svg>
        <div><b>Mon - Fri 9am - 6pm</b>Office hours</div>
      </div>
      <div class="socials" aria-label="Social links"><span></span><span></span><span></span></div>
    </div>
    <div class="footer-cols">
      <section>
        <h4>About Us</h4>
        <p>We help businesses in technology, defense, healthcare and professional services speak with clarity and earn lasting trust.</p>
      </section>
      <section>
        <h4>Recent News</h4>
        <p>How to prepare for your first TV interview<time>April 2, 2015</time></p>
        <p>Five steps to a calmer crisis response<time>March 28, 2015</time></p>
      </section>
      <section>
        <h4>Quick Links</h4>
        <ul><li>Services</li><li>Case Studies</li><li>Careers</li><li>Contact</li></ul>
      </section>
    </div>
  </div>
</footer>
<div class="bottom-bar">
  <div class="wrap">
    <span>© 2015 TRELVOX Studio. All rights reserved.</span>
    <nav><span>Home</span><span>About Us</span><span>Services</span><span>News</span><span>Contact</span></nav>
  </div>
</div>

</body>
</html>
```